We need letterhead, Business Cards, and envelops designed. We have attached a design of our logo and a sample of letterhead idea that was started but never perfected, it is only an idea for the letterhead if you can design something better we may love that also we are open to change.
We want a design that looks professional in style. we are a non profit trade association in the construction industry. the green color in the attached design represent green building, and we like that. also if you just want to enhance the letterhead sample that we attached that would be fine also.
Thanks and good luck
also the name that should show on the first business cards should be Morgan Feltwick, Director are web address is www.pvtrn.org

```html
<!DOCTYPE html>
<html lang="en">
<head>
<meta charset="utf-8">
<title>PVTRN Letterhead</title>
<link href="https://fonts.googleapis.com/css2?family=Arimo:wght@400;700&family=Montserrat:wght@400;600&display=swap" rel="stylesheet">
<style>
  :root {
    --backdrop: #e4e5e6;
    --paper: #ffffff;
    --ink: #1a1a1a;
    --muted: #7a7c7e;
    --green: #4c9a2a;
    --green-pale: #dfe8d6;
    --black: #0c0c0c;
  }
  html, body {
    margin: 0;
    width: 1200px;
    height: 909px;
    overflow: hidden;
    background: var(--backdrop);
  }
  .letterhead {
    position: absolute;
    left: 268px;
    top: 24px;
    width: 665px;
    height: 860px;
    background: var(--paper);
    box-shadow: 0 6px 24px rgba(0,0,0,.18);
    overflow: hidden;
    font-family: "Arimo", Arial, sans-serif;
    color: var(--ink);
  }
  .brand {
    position: absolute;
    left: 52px;
    top: 46px;
  }
  .brand-name {
    font-family: "Arimo", Arial, sans-serif;
    font-weight: 700;
    font-size: 40px;
    letter-spacing: 3px;
    line-height: 1;
    color: var(--ink);
    display: flex;
    align-items: center;
    gap: 10px;
  }
  .brand-mark {
    width: 14px;
    height: 14px;
    background: var(--green);
  }
  .brand-tagline {
    margin-top: 5px;
    font-size: 8.5px;
    letter-spacing: .4px;
    color: var(--ink);
  }
  .sender-address {
    position: absolute;
    right: 60px;
    top: 48px;
    font-family: "Montserrat", Arial, sans-serif;
    font-style: normal;
    font-size: 8px;
    letter-spacing: 1.4px;
    line-height: 1.5;
    color: var(--muted);
  }
  .letter {
    position: absolute;
    left: 52px;
    top: 140px;
    width: 560px;
    font-size: 10.5px;
    line-height: 1.45;
  }
  .recipient { margin: 0 0 18px; }
  .letter p { margin: 0 0 14px; }
  .signoff { margin-top: 22px; }
  .signature-name { margin-top: 34px; }
  .footer-art {
    position: absolute;
    left: 0;
    bottom: 0;
    width: 665px;
    height: 320px;
  }
  .footer-contact {
    position: absolute;
    right: 40px;
    bottom: 240px;
    font-family: "Montserrat", Arial, sans-serif;
    font-size: 9px;
    letter-spacing: 1.2px;
    color: var(--muted);
    display: flex;
    gap: 16px;
    align-items: center;
  }
  .footer-contact span { display: flex; align-items: center; gap: 5px; }
  .footer-web {
    position: absolute;
    right: 40px;
    bottom: 70px;
    font-family: "Montserrat", Arial, sans-serif;
    font-size: 13px;
    letter-spacing: 3px;
    color: #ffffff;
  }
</style>
</head>
<body>
<main class="letterhead">
  <header class="brand">
    <div class="brand-name"><span>PVTRN</span><span class="brand-mark"></span></div>
    <div class="brand-tagline">Pacific Valley Trades Network</div>
  </header>

  <address class="sender-address">
    address 4321<br>first street anytown<br>State ZIP
  </address>

  <section class="letter">
    <p class="recipient">June 26, 2014<br>Trenz Pruca<br>Title<br>Company Name<br>4321 First Street<br>Anytown, State ZIP</p>
    <p>Dear Trenz,</p>
    <p>Thank you for your continued support of our association and its members across the region. This year our trade partners completed more green building projects than ever before, and we are proud of the standards they keep. We invite you to review the enclosed summary of our work and share it with your team.</p>
    <p>Our training sessions on licensing, safety and efficient materials will resume next month. Each session is open to members at no cost, and seating is limited, so we ask that you reserve a place early. Course outlines and dates are listed on our website, along with contact details for each instructor.</p>
    <p>We also welcome your ideas for the coming year. Members who wish to join a committee or host a site visit may reply to this letter or call our office during business hours.</p>
    <p>Thank you again for your time. We look forward to working with you and your company in the months ahead.</p>
    <p class="signoff">Sincerely yours,</p>
    <p class="signature-name">Urna Semper</p>
  </section>

  <svg class="footer-art" viewBox="0 0 665 320">
    <rect x="40" y="120" width="230" height="170" fill="var(--green-pale)" opacity=".7" role="img" aria-label="Faint illustration of buildings and a house"/>
    <path d="M0 300 Q330 262 665 92 L665 104 Q330 274 0 312 Z" fill="var(--green)"/>
    <path d="M0 312 Q330 274 665 104 L665 320 L0 320 Z" fill="var(--black)"/>
  </svg>

  <div class="footer-contact">
    <span><svg width="9" height="9" viewBox="0 0 10 10"><path d="M2 1h2l1 2-1.2 1a6 6 0 0 0 2.2 2.2L7 5l2 1v2a1 1 0 0 1-1 1A8 8 0 0 1 1 2a1 1 0 0 1 1-1z" fill="var(--green)"/></svg>123-456-7890</span>
    <span><svg width="9" height="9" viewBox="0 0 10 10"><rect x="1" y="3" width="8" height="6" rx="1" fill="var(--green)"/><rect x="3" y="1" width="4" height="3" fill="var(--green)"/></svg>123-456-7891</span>
  </div>
  <div class="footer-web">www.pvtrn.org</div>
</main>
</body>
</html>
```